Business Card for Vorla Parts Wholesale supplier

Hi There! I need a new business card for our company. We are specialized in selling Vorla parts, mostly we sell new LCD screens for Zelnar and Drelks. I would like to see that back in the design.

You can find the colors and logo's on our website: www.hartuvo.nl

Industry/Entity Type

Business

Contact Information for Business Card

My Details:
Tobias Lindqvist

Phone: 0031687203316
E-mail: Tobias@hartuvo.nl

Slogan: "Because Quality Matters"

Font styles to use
Sans Serif

Colors

Designer to choose colors to be used in the design.

Requirements
Must have
• A Black backside with the Hartuvo logo on it. The front side should be clean with only my contact details.
• But I'm also open for something really different or awesome!
Nice to have
• Remember that we are in the parts & repairing industry, So i'll be handing those business cards mainly to repair companies. Maybe you can do something with that thought :)

```html
<!DOCTYPE html>
<html lang="en">
<head>
<meta charset="utf-8">
<title>Hartuvo Business Card</title>
<link rel="stylesheet" href="https://fonts.googleapis.com/css2?family=Exo+2:wght@400;500;600;700;800&display=swap">
<style>
  :root {
    --stage: #080808;
    --paper: #ffffff;
    --brand-orange: #f27324;
    --ink: #111111;
    --on-orange: #ffffff;
  }
  * { margin: 0; padding: 0; box-sizing: border-box; }
  html, body {
    width: 1200px; height: 900px; overflow: hidden;
    background: var(--stage);
    font-family: "Exo 2", Arial, sans-serif;
  }
  .stage { position: relative; width: 1200px; height: 900px; }

  .card {
    position: absolute; top: 184px; height: 491px;
    border-radius: 14px; overflow: hidden;
  }
  .card-front { left: 299px; width: 301px; background: var(--paper); }
  .card-back { left: 645px; width: 305px; background: var(--brand-orange); }

  .front-brand {
    position: absolute; left: 31px; top: 290px; top: 106px;
    display: flex; align-items: center; gap: 10px;
  }
  .front-brand .brand-mark {
    width: 40px; height: 40px; background: var(--brand-orange); border-radius: 6px;
  }
  .front-brand .brand-name {
    font-size: 44px; font-weight: 700; color: var(--ink); letter-spacing: 0.5px; line-height: 1;
  }

  .holder-name {
    position: absolute; left: 30px; top: 278px;
    font-size: 23px; font-weight: 700; color: var(--brand-orange); letter-spacing: 0.3px;
    text-transform: uppercase;
  }
  .contact-list {
    position: absolute; left: 31px; top: 316px; list-style: none;
  }
  .contact-list li {
    display: flex; align-items: center; gap: 7px;
    height: 22px; font-size: 14px; color: var(--ink);
  }
  .contact-list svg { width: 14px; height: 14px; flex: none; }

  .slogan-band {
    position: absolute; left: 0; bottom: 0; width: 100%; height: 87px;
    background: var(--brand-orange);
    display: flex; align-items: center; justify-content: center;
    color: var(--on-orange); font-size: 17px; font-weight: 500; letter-spacing: 0.2px;
  }

  .back-brand {
    position: absolute; left: 0; top: 214px; width: 100%; text-align: center;
    font-size: 56px; font-weight: 700; color: var(--on-orange); line-height: 1; letter-spacing: 0.5px;
  }
  .back-tagline {
    position: absolute; left: 0; top: 420px; width: 100%; text-align: center;
    font-size: 16px; font-weight: 600; color: var(--on-orange);
  }
</style>
</head>
<body>
<main class="stage">
  <section class="card card-front" aria-label="Business card front">
    <div class="front-brand">
      <span class="brand-mark"></span>
      <span class="brand-name">hartuvo</span>
    </div>
    <h1 class="holder-name">Tobias Lindqvist</h1>
    <ul class="contact-list">
      <li>
        <svg viewBox="0 0 14 14" aria-hidden="true"><circle cx="7" cy="7" r="7" fill="var(--brand-orange)"/><path d="M4 5.2c0-.8 1.2-1.4 3-1.4s3 .6 3 1.4v.6H8.6v-.7H5.4v.7H4z M4.3 9.8 5.3 6.6h3.4l1 3.2z" fill="#fff"/></svg>
        0031687203316
      </li>
      <li>
        <svg viewBox="0 0 14 14" aria-hidden="true"><circle cx="7" cy="7" r="7" fill="var(--brand-orange)"/><rect x="3.6" y="4.6" width="6.8" height="4.8" rx="0.6" fill="#fff"/><path d="M3.8 4.9 7 7.4l3.2-2.5" fill="none" stroke="var(--brand-orange)" stroke-width="0.8"/></svg>
        Tobias@hartuvo.nl
      </li>
      <li>
        <svg viewBox="0 0 14 14" aria-hidden="true"><circle cx="7" cy="7" r="7" fill="var(--brand-orange)"/><circle cx="7" cy="7" r="3.4" fill="none" stroke="#fff" stroke-width="0.9"/><path d="M3.6 7h6.8M7 3.6c-1.6 1.9-1.6 4.9 0 6.8M7 3.6c1.6 1.9 1.6 4.9 0 6.8" fill="none" stroke="#fff" stroke-width="0.7"/></svg>
        www.hartuvo.nl
      </li>
    </ul>
    <div class="slogan-band">Because Quality Matters</div>
  </section>

  <section class="card card-back" aria-label="Business card back">
    <div class="back-brand">hartuvo</div>
    <p class="back-tagline">The highest quality OEM parts</p>
  </section>
</main>
</body>
</html>
```